Web Design Project

Hi, we need a new and professional design for our company "partnertradecircuitry". The website should communicate business but with a friendly and professional touch.

You can use the following categories for the menu;

Home - customer groups - products - voucher system- contact

Give it your best,

Regards,
Oswin

Industry/Entity Type

Business

```html
<!DOCTYPE html>
<html lang="en">
<head>
<meta charset="utf-8">
<title>partnertradecircuitry — Business</title>
<link href="https://fonts.googleapis.com/css2?family=Roboto+Condensed:wght@400;700&family=Open+Sans:wght@400;600;700&display=swap" rel="stylesheet">
<style>
  :root {
    --page-bg: #e6e4dc;
    --panel-bg: #ffffff;
    --ink: #3a3a3a;
    --ink-soft: #7a7a7a;
    --body-text: #4a4a4a;
    --link-blue: #1f5fae;
    --date-blue: #2f7fc8;
    --nav-bg: #f1f0eb;
    --nav-edge: #d9d7cf;
    --contact-bg: #c8bf98;
    --contact-ink: #4c4838;
    --banner-blue: #1559b8;
    --rule: #9a9a9a;
    --dots: #b8b8b8;
  }
  * { box-sizing: border-box; margin: 0; padding: 0; }
  html, body { width: 1200px; height: 1128px; overflow: hidden; }
  body {
    position: relative;
    background: linear-gradient(180deg, #ebe9e2 0%, var(--page-bg) 100%);
    font-family: "Open Sans", Arial, sans-serif;
    color: var(--body-text);
  }
  .abs { position: absolute; }

  .main-panel {
    left: 345px; top: 36px; width: 836px; height: 1018px;
    background: var(--panel-bg); border-radius: 10px;
    box-shadow: 0 3px 8px rgba(0,0,0,0.18);
  }

  .clock { left: 86px; top: 70px; font-size: 14px; color: #6a6a6a; }
  .clock b { color: #4a4a4a; font-weight: 700; }
  .clock .time { margin-left: 16px; font-weight: 700; color: #4a4a4a; font-size: 15px; }

  .utility-icon { top: 68px; width: 20px; height: 20px; }
  .utility-sep { top: 64px; width: 1px; height: 28px; background: #d0d0d0; }

  .banner {
    left: 19px; top: 114px; width: 1162px; height: 188px;
    background: linear-gradient(90deg, #d9c3a2 0%, #ead7bb 22%, #cfb08a 30%, #6f8f4a 45%, #3d7a2a 50%, #d8c1a3 58%, #efe4d2 75%, #f3ede4 100%);
    border-radius: 6px 6px 0 0;
    box-shadow: 0 2px 5px rgba(0,0,0,0.2);
  }
  .brand-name {
    left: 36px; top: 176px;
    font-family: "Roboto Condensed", Arial, sans-serif;
    font-weight: 700; font-size: 34px; color: #2aa7dc;
  }
  .tagline-box {
    left: 736px; top: 154px; width: 268px; height: 105px;
    background: linear-gradient(180deg, #2a74cf, var(--banner-blue));
    border-radius: 6px 0 0 6px;
    color: #fff; font-family: "Roboto Condensed", Arial, sans-serif;
    padding: 16px 0 0 26px;
  }
  .tagline-box .big { font-size: 42px; letter-spacing: 1px; line-height: 1; }
  .tagline-box .small { font-size: 22px; line-height: 1.3; }
  .banner-art {
    left: 975px; top: 96px; width: 200px; height: 200px;
    background: linear-gradient(160deg, #f6f6f6, #c9ced6);
    border-radius: 8px; transform: rotate(-12deg);
  }

  .main-nav { left: 34px; top: 312px; width: 311px; }
  .nav-item {
    height: 78px; margin-bottom: 10px;
    background: linear-gradient(180deg, #f5f4f0, var(--nav-bg));
    border: 1px solid var(--nav-edge); border-right: none;
    border-radius: 6px 0 0 6px;
    padding: 14px 0 0 31px;
    box-shadow: 0 2px 3px rgba(0,0,0,0.08);
  }
  .nav-item .label {
    font-family: "Roboto Condensed", Arial, sans-serif;
    font-weight: 700; font-size: 22px; color: var(--ink); line-height: 1.1;
  }
  .nav-item .sub { font-size: 15px; color: var(--ink-soft); line-height: 1.2; }

  .contact-card {
    left: 34px; top: 849px; width: 311px; height: 157px;
    background: var(--contact-bg); border-radius: 8px 0 0 8px;
    padding: 14px 0 0 46px; color: var(--contact-ink);
    font-size: 16px; line-height: 1.35;
  }
  .contact-card h3 {
    font-family: "Roboto Condensed", Arial, sans-serif; font-weight: 400;
    font-size: 27px; color: #55503c; margin-bottom: 4px;
  }
  .contact-card .company { font-weight: 700; }

  .photo { border-radius: 8px; border: 1px solid #bbb; }
  .welcome-photo { left: 393px; top: 382px; width: 208px; height: 172px;
    background: linear-gradient(135deg, #ede7dd, #d8c8b2 55%, #a9a49a); }

  .heading {
    font-family: "Roboto Condensed", Arial, sans-serif;
    font-weight: 700; font-size: 31px; color: var(--ink);
    letter-spacing: -0.5px; line-height: 1.05;
  }
  .subheading {
    font-family: "Roboto Condensed", Arial, sans-serif;
    font-size: 19px; color: var(--ink-soft); line-height: 1.1;
  }
  .copy { font-size: 16px; line-height: 21px; color: var(--body-text); }
  .read-more { font-size: 16px; color: var(--link-blue); text-align: right; }
  .read-more::before { content: "|"; color: #999; margin-right: 4px; }
  .read-more::after { content: "|"; color: #999; margin-left: 4px; }
  .read-more span::before { content: "›"; color: #999; margin-right: 6px; font-size: 14px; }

  .welcome-title { left: 631px; top: 375px; }
  .welcome-copy { left: 631px; top: 454px; width: 490px; }
  .welcome-more { left: 800px; top: 563px; width: 330px; }

  .priority-title { left: 393px; top: 626px; }
  .priority-rule { left: 393px; top: 691px; width: 336px; height: 2px; background: var(--rule); }
  .priority-copy { left: 393px; top: 721px; width: 340px; }
  .priority-list { left: 393px; top: 843px; width: 336px; list-style: none; }
  .priority-list li {
    height: 28px; padding-left: 32px; font-size: 16px; line-height: 24px;
    color: var(--link-blue); border-bottom: 2px dotted var(--dots); position: relative;
  }
  .priority-list li::before {
    content: ""; position: absolute; left: 16px; top: 11px;
    width: 5px; height: 5px; border: 1px solid #999; border-radius: 50%;
  }

  .column-divider { left: 761px; top: 616px; width: 1px; height: 368px; background: #a8a8a8; }

  .news-title { left: 794px; top: 626px; }
  .news-photo-1 { left: 794px; top: 727px; width: 130px; height: 89px;
    background: linear-gradient(135deg, #6e5c4a, #c9b39a 55%, #8c7f70); }
  .news-photo-2 { left: 794px; top: 882px; width: 130px; height: 89px;
    background: linear-gradient(135deg, #5f7a97, #d9cdbd 55%, #8a9cae); }
  .news-copy { left: 945px; width: 190px; }
  .news-copy .date { color: var(--date-blue); font-weight: 700; font-size: 19px; margin-right: 4px; }
  .news-item-1 { top: 719px; }
  .news-item-2 { top: 875px; }
  .news-more-1 { left: 1000px; top: 814px; width: 130px; }
  .news-more-2 { left: 1000px; top: 969px; width: 130px; }
  .news-sep { left: 794px; top: 866px; width: 336px; border-top: 2px dotted var(--dots); }

  .site-footer {
    left: 345px; top: 1070px; width: 836px; text-align: center;
    font-size: 15px; color: #555;
  }
  .site-footer .sep { margin: 0 6px; }
</style>
</head>
<body>

  <div class="abs main-panel"></div>

  <div class="abs clock"><b>FRI</b> 00.00.2013 <span class="time">5:45 PM</span></div>

  <svg class="abs utility-icon" style="left:398px" viewBox="0 0 20 20" aria-label="Home">
    <path d="M3 10 L10 4 L17 10 M5 9 V16 H15 V9" fill="none" stroke="#777" stroke-width="1.5"/>
  </svg>
  <div class="abs utility-sep" style="left:454px"></div>
  <svg class="abs utility-icon" style="left:488px" viewBox="0 0 20 20" aria-label="Page">
    <path d="M6 3 H12 L15 6 V17 H6 Z" fill="none" stroke="#777" stroke-width="1.5"/>
  </svg>
  <div class="abs utility-sep" style="left:545px"></div>
  <svg class="abs utility-icon" style="left:580px" viewBox="0 0 20 20" aria-label="Sitemap">
    <rect x="7" y="3" width="6" height="4" fill="none" stroke="#777" stroke-width="1.5"/>
    <rect x="2" y="13" width="6" height="4" fill="none" stroke="#777" stroke-width="1.5"/>
    <rect x="12" y="13" width="6" height="4" fill="none" stroke="#777" stroke-width="1.5"/>
    <path d="M10 7 V10 M5 13 V10 H15 V13" fill="none" stroke="#777" stroke-width="1.5"/>
  </svg>

  <div class="abs banner" role="img" aria-label="Header photo: hands holding a green globe on a wooden desk, with a clipboard and pen"></div>
  <div class="abs banner-art" role="img" aria-label="Clipboard with document and pen"></div>
  <div class="abs brand-name">partnertradecircuitry</div>
  <div class="abs tagline-box">
    <div class="big">INDIVIDUAL</div>
    <div class="small">CUSTOMERS APPROACH</div>
  </div>

  <nav class="abs main-nav">
    <div class="nav-item"><div class="label">Home</div><div class="sub">lorem empus</div></div>
    <div class="nav-item"><div class="label">Customer Groups</div><div class="sub">lorem epsum</div></div>
    <div class="nav-item"><div class="label">Products</div><div class="sub">lorum epsum</div></div>
    <div class="nav-item"><div class="label">Voucher System</div><div class="sub">lerum epsum</div></div>
    <div class="nav-item"><div class="label">Contact</div><div class="sub">lerum epsum</div></div>
  </nav>

  <div class="abs contact-card">
    <h3>Primary Contact</h3>
    <div class="company">The Company Name Inc.</div>
    <div>4120 - 4126 Orchard Lane,</div>
    <div>Brackley, QT14 3LW</div>
    <div><b>Phone:</b>&nbsp; +1 800 472 3915</div>
  </div>

  <div class="abs photo welcome-photo" role="img" aria-label="Portrait photo of a businesswoman"></div>
  <div class="abs welcome-title">
    <div class="heading">Welcome to our Company Website</div>
    <div class="subheading">Some words about company</div>
  </div>
  <p class="abs copy welcome-copy">Donec et tortor. Praesent iaculis vestibulum neque arcu tortor... fringilla ut, suscipit ac, condimentum sit amet, est. Praesent malesuada purus at dolor. Maecenas porttitor, ante nec pulvinar suscipit, ante nisl lobortis dui, eu malesuada pede tortor mollis wisi. Suspendisse egestas. Quisque enim...</p>
  <div class="abs read-more welcome-more"><span>read more about company</span></div>

  <div class="abs priority-title">
    <div class="heading">Priority line of business</div>
    <div class="subheading">Professional management and researches</div>
  </div>
  <div class="abs priority-rule"></div>
  <p class="abs copy priority-copy">Praesent malesuada purus at dolor. Suspendisse egestas. Quisque enim. Duis neque pede, ultrices sed, vulputate at, vestibulum id, nunc quisque orci quam, consectetuer quis, rhoncus sed...</p>
  <ul class="abs priority-list">
    <li>Praesent malesuada purus at dolor.</li>
    <li>Suspendisse egestas quisque enim.</li>
    <li>Duis neque pede ultrices sed vulput</li>
    <li>Quisque orci quam, consectetuer quis</li>
    <li>Rhoncus sed vehicula nec velit.</li>
  </ul>

  <div class="abs column-divider"></div>

  <div class="abs news-title">
    <div class="heading">Latest News</div>
    <div class="subheading">corporate highlights</div>
  </div>

  <div class="abs photo news-photo-1" role="img" aria-label="Photo of a smiling woman in an office"></div>
  <p class="abs copy news-copy news-item-1"><span class="date">21.05</span>Praesent iaculis vestibulum neque arcu tortor fringilla ut, suscipit ac, condimentum sit...</p>
  <div class="abs read-more news-more-1"><span>read more</span></div>

  <div class="abs news-sep"></div>

  <div class="abs photo news-photo-2" role="img" aria-label="Photo of a woman talking on the phone"></div>
  <p class="abs copy news-copy news-item-2"><span class="date">15.05</span>Praesent male-suada purus at dolor. Maecenas porttitor, ante nec pulvinar suscipit...</p>
  <div class="abs read-more news-more-2"><span>read more</span></div>

  <footer class="abs site-footer">partnertradecircuitry.Com © 2013<span class="sep">|</span>Privacy Policy<span class="sep">|</span>Terms Of Use</footer>

</body>
</html>
```